The quiet harbor with an elephant incorporated in the background

Target Market(s)

Real estate

Industry/Entity Type

Real Estate

Contact Information for Business Card

On back on want my name & number
In front I want the business name, "the quiet harbor", below to say staging & design

Logo Text

The quiet harbor

Font styles to use
Serif

Colors
000000

Requirements
Must have
• I want an elephant behind the writing in gold transperant

```html
<!DOCTYPE html>
<html lang="en">
<head>
<meta charset="utf-8">
<title>The Quiet Harbor — Business Card</title>
<link rel="stylesheet" href="https://fonts.googleapis.com/css2?family=Crimson+Text:wght@400&family=Poppins:wght@400&display=swap">
<style>
  :root {
    --backdrop: #e6e6e6;
    --card: #fbfbfa;
    --ink: #1f1f1f;
    --gold: #c9a86a;
    --gold-light: #e0c48c;
    --gold-deep: #a8823f;
    --muted: #555555;
  }
  * { margin: 0; padding: 0; box-sizing: border-box; }
  html, body {
    width: 1200px;
    height: 1000px;
    overflow: hidden;
    background: var(--backdrop);
  }
  .sheet {
    position: relative;
    width: 1200px;
    height: 1000px;
  }
  .card {
    position: absolute;
    top: 344px;
    width: 540px;
    height: 312px;
    background: var(--card);
    box-shadow: 0 2px 6px rgba(0, 0, 0, 0.18);
    overflow: hidden;
  }
  .card-front { left: 30px; }
  .card-back { left: 630px; }

  .elephant-art {
    position: absolute;
    left: 95px;
    top: 54px;
    width: 169px;
    height: 152px;
    border-radius: 40% 45% 20% 20%;
    background: radial-gradient(ellipse at 45% 40%, var(--gold-light), var(--gold) 55%, var(--gold-deep));
    opacity: 0.85;
  }
  .name-frame {
    position: absolute;
    left: 44px;
    top: 115px;
    width: 447px;
    height: 29px;
    border: 2px solid var(--ink);
    display: flex;
    align-items: center;
    justify-content: center;
    gap: 26px;
    font-family: "Crimson Text", serif;
    font-size: 19px;
    letter-spacing: 0.55em;
    text-transform: uppercase;
    line-height: 1;
  }
  .name-first { color: var(--ink); }
  .name-last { color: var(--gold); }

  .contact {
    position: absolute;
    left: 0;
    right: 0;
    top: 260px;
    text-align: center;
    font-family: "Poppins", sans-serif;
    font-size: 9.5px;
    line-height: 17px;
    color: var(--muted);
  }

  .business-name {
    position: absolute;
    inset: 0;
    display: flex;
    align-items: center;
    justify-content: center;
    font-family: "Crimson Text", serif;
    font-size: 27px;
    color: var(--ink);
  }
</style>
</head>
<body>
  <main class="sheet">
    <section class="card card-front">
      <div class="elephant-art" role="img" aria-label="Gold elephant figure standing behind the name, trunk raised"></div>
      <div class="name-frame">
        <span class="name-first">Adrian</span>
        <span class="name-last">Vale</span>
      </div>
      <div class="contact">
        <p>000 000 0000 | 000 000 0000 | info@yourmail.com| www.yourweb.com</p>
        <p>your street address, Gpo-000 state, country</p>
      </div>
    </section>

    <section class="card card-back">
      <h1 class="business-name">The Quiet Harbor</h1>
    </section>
  </main>
</body>
</html>
```